Poster & Flyer - Golf Tournament

Poster and Flyer (2 sperapate) is required for an upcoming Torvenne Classic Golf Tournament. Although this tournament is amongst friends only (normally 40 people) we want to announce this years (13th year) tournament a bit differently.

* Poster should grab the players (brief outline)
* Flyer should have more detail and graphics
* Design flows in each Poster/Flyer.

There are several components to the Tournament that include:

1. Tournament Logo
2. Prizes (Set of golf clubs and Hotel Accommodation)
3. FairwayLogix App (Live leaderboard)
4. Timetable of events and golf
5. Venue of Golf Tournament
6. Payment terms

All information relating to components are attached.

1. Tournament Logo - Some brief background, The "Torvenne" was religious compass like symbol that basically pointed the people in the right direction when they were being faithful. We have incorporated the Logo with a golf tournament :-).

2. 1st Prize - full set of Fitted Harrier ZEN Flux Max Golf Clubs with ZEN Golf Bag (Worth $2, 200 RRP)

2nd Prize - 2 nights 5 Star Accommodation at any Brenmore Hotel in Australia includes Breakfast. (Worth $700 RRP).

Fairway Logix is a free mobile Golf app that will take the Torvenne Classic to another level.

Easy mobile live scoring, leaderboards, chat, stats & social interactions - all real time with all popular game formats.

Bring it On!

More info go to http://www.fairwaylogix.example/

* Can you incorporate some graphics from website in Poster and Flyer.

4. Timetable document attached. Make it presentable on the Flyer.

5. If we can incorporate aspects (graphics) of the golf course e.g. Golf Course Logo's, signature holes etc.

Go to:

a. Tamblin Vale Course - http://www.tamblinvale.example.au
b. Mount Orrin Golf Resort - https://www.vtma.example.au/wps/wcm/connect/vtma/Resorts/VTMA+Resorts/VTMA+Mount+Orrin+Resort/Mount+Orrin+Golf

If you go to findora images I'm sure you can find further images relating to the golf course.

6. Payment terms: Can you please express the "early bird special"

Also I will need a extra poster without the "early bird special" once the time runs out.

If you have any further questions please do not hesitate to drop me an email.

* Please note - I will end Project early if I find a design I desire.
Updates

Please add "like us on chatterbook" logo (see attached)

chatterbook link is - http://www.chatterbook.example/Torvenneclassic

```html
<!DOCTYPE html>
<html lang="en">
<head>
<meta charset="utf-8">
<title>Torvenne Classic Golf Tournament</title>
<link rel="stylesheet" href="https://fonts.googleapis.com/css2?family=Raleway:wght@300;400;600;700;800&display=swap">
<style>
:root{
  --green-dark:#2d5a1b;
  --green:#4f7d2c;
  --grey-dark:#4e5256;
  --grey:#6b6f73;
  --ball-edge:#c8c9cb;
  --gold:#c7a24a;
  --white:#ffffff;
}
*{margin:0;padding:0;box-sizing:border-box}
html,body{width:848px;height:1200px;overflow:hidden;background:var(--white)}
body{font-family:'Raleway',sans-serif;color:var(--grey-dark)}
.poster{position:relative;width:848px;height:1200px;overflow:hidden}
.course-photo{position:absolute;inset:0;
  background:linear-gradient(180deg,#eef0ee 0%,#d9ded6 12%,#a9b79a 24%,#6e9a3d 34%,#4f8a24 48%,#cfb58d 52%,#6ea32e 60%,#3f7c1c 80%,#2f6a17 100%)}
.ball-shape{position:absolute;inset:0}
.dashes{position:absolute;inset:0}
.badge{position:absolute;border-radius:50%;
  background:radial-gradient(circle at 45% 40%,#ffffff 0%,#f1f1f1 55%,#d2d3d5 100%);
  box-shadow:2px 3px 6px rgba(0,0,0,.25);
  display:flex;flex-direction:column;align-items:center;justify-content:center;text-align:center}
.badge--year{left:-24px;top:65px;width:180px;height:180px}
.badge--price{left:-24px;top:282px;width:180px;height:180px}
.badge--app{left:-24px;top:560px;width:180px;height:180px}
.badge-line{line-height:.95;padding-left:30px}
.badge-line--light{font-weight:300;color:var(--green);font-size:42px}
.badge-line--grey{font-weight:600;color:var(--grey);font-size:42px}
.badge-line--bold{font-weight:800;color:var(--grey-dark);font-size:44px}
.title{position:absolute;left:184px;top:108px;text-align:center;width:200px;line-height:1}
.title-top{font-weight:800;color:var(--green-dark);font-size:30px}
.title-bottom{font-weight:400;color:var(--grey-dark);font-size:30px}
.early-bird{position:absolute;left:204px;top:303px;width:196px;height:29px;background:#54585c;
  color:var(--white);font-size:15px;font-weight:400;display:flex;align-items:center;justify-content:center;letter-spacing:.2px}
.early-bird b{font-weight:800;margin-right:4px}
.terms{position:absolute;left:210px;top:345px;width:240px;font-size:11.5px;line-height:23px;color:var(--green-dark)}
.terms em{font-style:normal;color:var(--green);font-weight:600}
.terms .note{display:block;padding-left:4px}
.app{position:absolute;left:176px;top:624px;width:250px;text-align:center;line-height:.95}
.app-top{font-weight:800;color:var(--grey-dark);font-size:40px}
.app-bottom{font-weight:400;color:var(--green);font-size:37px}
.app-url{font-weight:600;color:var(--green-dark);font-size:15px;margin-top:2px}
.prize-photo{position:absolute;left:216px;top:725px;width:170px;height:170px;border-radius:50%;
  border:4px solid #9a9b9d;background:linear-gradient(135deg,#1c2a55 0%,#2b4aa8 35%,#e6e6e6 55%,#d8692a 85%,#b24f1a 100%)}
.prize{position:absolute;text-align:center;line-height:.95}
.prize--first{left:10px;top:815px;width:165px}
.prize--second{left:180px;top:995px;width:160px}
.prize-rank{font-weight:300;color:var(--green);font-size:28px}
.prize-item{font-weight:800;color:var(--grey-dark);font-size:32px}
.prize-note{font-size:7.5px;color:var(--grey-dark);font-weight:400;margin-top:2px}
.hotel-mark{position:absolute;left:23px;top:937px;width:132px;height:132px;border-radius:50%;
  background:var(--white);border:6px solid #a9aaac;box-shadow:1px 2px 5px rgba(0,0,0,.2);
  display:flex;align-items:center;justify-content:center;font-weight:700;color:#1e3f9a;font-size:24px}
.schedule{position:absolute;left:560px;top:28px;width:280px;text-align:center;color:#2c2c2c}
.day{font-weight:800;color:var(--green-dark);font-size:17px;margin:0 0 8px}
.day + ul{margin-bottom:14px}
.schedule ul{list-style:none;font-size:11.5px;line-height:16px}
.event-brand{position:absolute;left:500px;top:1040px;width:290px;text-align:center;color:var(--gold);font-weight:600}
.event-brand-dot{width:44px;height:44px;border-radius:50%;background:var(--gold);margin:0 auto 16px}
.event-brand-name{font-size:30px;letter-spacing:3px;line-height:1}
.event-brand-sub{font-size:16px;letter-spacing:6px;margin-top:4px}
</style>
</head>
<body>
<main class="poster">
  <div class="course-photo" role="img" aria-label="Golf course photo: golfer in red shirt playing from a bunker beside a green with flag, trees and sky behind"></div>

  <svg class="ball-shape" width="848" height="1200" viewBox="0 0 848 1200" aria-hidden="true">
    <defs>
      <linearGradient id="ballFill" x1="0" y1="0" x2="1" y2="0">
        <stop offset="0.78" stop-color="#ffffff"/>
        <stop offset="0.93" stop-color="#ececec"/>
        <stop offset="1" stop-color="#bfc0c2"/>
      </linearGradient>
    </defs>
    <path d="M0 0 H300 C480 150 625 400 592 625 C570 850 505 1050 452 1200 H0 Z" fill="url(#ballFill)"/>
  </svg>

  <svg class="dashes" width="848" height="1200" viewBox="0 0 848 1200" aria-hidden="true">
    <g fill="none" stroke="#9a9b9d" stroke-width="2" stroke-dasharray="14 12">
      <path d="M150 195 Q195 240 152 292"/>
      <path d="M150 440 Q200 510 152 590"/>
      <path d="M150 700 Q210 715 232 760"/>
      <path d="M222 872 Q170 895 140 945"/>
    </g>
  </svg>

  <div class="badge badge--year">
    <span class="badge-line badge-line--grey">13th</span>
    <span class="badge-line badge-line--light">YEAR</span>
  </div>
  <div class="title">
    <div class="title-top">GOLF</div>
    <div class="title-bottom">TOURNAMENT</div>
  </div>

  <div class="badge badge--price">
    <span class="badge-line badge-line--light">ONLY</span>
    <span class="badge-line badge-line--bold">595 $</span>
  </div>
  <div class="early-bird"><b>EARLY BIRD</b> PRICE</div>
  <p class="terms">
    a)Get a <em>$65</em> savings when you pay the total of $530 upfront before 15th July 2013.<br>
    b)or Pay <em>$300</em> before the 30th June to secure your place. The remaining <em>$295</em> to be paid before the 30th Sept.<br>
    <span class="note">• Due to individual cancellations we can only refund money if someone replaces your spot.</span>
  </p>

  <div class="badge badge--app">
    <span class="badge-line badge-line--light">MOB</span>
    <span class="badge-line badge-line--bold">APP</span>
  </div>
  <div class="app">
    <div class="app-top">FAIRWAY</div>
    <div class="app-bottom">LOGIX</div>
    <div class="app-url">www.fairwaylogix.example</div>
  </div>

  <div class="prize-photo" role="img" aria-label="Photo of golf bags in blue, white and orange"></div>
  <div class="prize prize--first">
    <div class="prize-rank">1ST PLACE</div>
    <div class="prize-item">FULL SET</div>
    <div class="prize-note">Fitted Harrier ZEN Flux Max Golf Clubs</div>
  </div>

  <div class="hotel-mark">Brenmore</div>
  <div class="prize prize--second">
    <div class="prize-rank">2ND PLACE</div>
    <div class="prize-item">5* HOTEL</div>
    <div class="prize-note">INCLUDING BREAKFAST</div>
  </div>

  <section class="schedule">
    <h2 class="day">Tuesday</h2>
    <ul>
      <li>• Check in VTMA Mount Orrin Resort,</li>
      <li>Kelby Drive, Mount Orrin VIC 3939</li>
    </ul>
    <h2 class="day">Thursday</h2>
    <ul>
      <li>• Buffet Breakfast – Mount Orrin</li>
      <li>• am - Stroke - Mount Orrin</li>
      <li>• pm - 4 man Ambrose</li>
      <li>• Dinner &amp; Presentations</li>
    </ul>
    <h2 class="day">Wednesday</h2>
    <ul>
      <li>• Buffet Breakfast – Mount Orrin</li>
      <li>• am - Stableford - Tamblin Vale Golf Course</li>
      <li>• pm - 4 man Ambrose</li>
      <li>• Dinner - Mount Orrin</li>
      <li>• Harbourline Hot Springs</li>
    </ul>
  </section>

  <div class="event-brand">
    <div class="event-brand-dot"></div>
    <div class="event-brand-name">THE TORVENNE</div>
    <div class="event-brand-sub">CLASSIC</div>
  </div>
</main>
</body>
</html>
```